Childcare Stationery( business cards, letter head, envelopes and letter size folders)
Maple Hill Early Education Center
Modern
Darnetta Okonkwo-Vale
728 West Linden Avenue
Columbus, Ohio 43287
darnettaov@maplehillkidz.com
www.maplehillkidz.com
Learn, Explore, Bloom
Please use logo and colors.

```html
<!DOCTYPE html>
<html lang="en">
<head>
<meta charset="utf-8">
<title>Maple Hill Early Education Center – Business Cards</title>
<link href="https://fonts.googleapis.com/css2?family=Nunito:wght@400;700;800&display=swap" rel="stylesheet">
<style>
  :root{
    --page:#ecebe8;
    --card-white:#ffffff;
    --brand-blue:#2aa8df;
    --brand-blue-deep:#1f8fc2;
    --brand-green:#8cc63f;
    --brand-green-deep:#6b9f2b;
    --ink:#555a5e;
    --white:#ffffff;
  }
  *{box-sizing:border-box;margin:0;padding:0}
  html,body{width:1200px;height:908px;overflow:hidden}
  body{background:var(--page);font-family:"Nunito",Arial,sans-serif;position:relative}
  .card{position:absolute;width:520px;height:296px;border-radius:14px;overflow:hidden;box-shadow:0 6px 18px rgba(0,0,0,.12)}
  .card--front{left:60px;top:110px;background:var(--card-white)}
  .card--back-white{left:620px;top:110px;background:var(--card-white)}
  .card--back-blue{left:60px;top:502px;background:var(--brand-blue)}
  .card--back-green{left:620px;top:502px;background:var(--brand-green)}

  .brand{display:flex;align-items:center;gap:12px;position:absolute}
  .brand__dot{width:54px;height:54px;border-radius:50%;background:var(--brand-green);flex:none}
  .brand__name{font-weight:800;font-size:40px;line-height:1;color:var(--brand-blue);white-space:nowrap}
  .card--back-blue .brand__dot,.card--back-green .brand__dot{background:var(--white)}
  .card--back-blue .brand__name,.card--back-green .brand__name{color:var(--white)}

  .card--front .brand{left:26px;top:58px}
  .card--front .brand__dot{width:44px;height:44px}
  .card--front .brand__name{font-size:32px}
  .card--back-white .brand,.card--back-blue .brand,.card--back-green .brand{left:50%;top:92px;transform:translateX(-50%)}

  .divider{position:absolute;left:272px;top:36px;width:2px;height:124px;background:var(--brand-blue)}
  .contact{position:absolute;left:288px;top:34px;color:var(--ink);font-size:12.5px;line-height:1.5}
  .contact__name{color:var(--brand-blue);font-weight:700;font-size:17px;margin-bottom:20px}
  .contact__gap{height:8px}

  .wave{position:absolute;left:0;bottom:0;width:520px;height:120px}
  .web{position:absolute;right:26px;bottom:24px;color:var(--white);font-weight:700;font-size:15px}

  .tagline-band{position:absolute;left:0;right:0;bottom:34px;height:36px;display:flex;align-items:center;justify-content:center;font-weight:800;font-size:19px;color:var(--white)}
  .card--back-white .tagline-band{background:var(--brand-blue)}
  .card--back-blue .tagline-band{background:var(--brand-blue-deep);border-top:3px solid var(--white);border-bottom:3px solid var(--white)}
  .card--back-green .tagline-band{background:var(--brand-green-deep)}
  .rule{position:absolute;left:0;right:0;bottom:20px;height:4px}
  .card--back-white .rule{background:var(--brand-blue)}
  .card--back-green .rule{background:var(--brand-green-deep)}
</style>
</head>
<body>
  <section class="card card--front" aria-label="Business card front">
    <div class="brand"><span class="brand__dot"></span><span class="brand__name">Maple Hill</span></div>
    <div class="divider"></div>
    <div class="contact">
      <p class="contact__name">Darnetta Okonkwo-Vale</p>
      <p>728 West Linden Avenue</p>
      <p>Columbus, Ohio 43287</p>
      <div class="contact__gap"></div>
      <p>C: 614-555-0182</p>
      <p>E: darnettaov@maplehillkidz.com</p>
    </div>
    <svg class="wave" viewBox="0 0 520 120" aria-hidden="true">
      <path d="M0 52 C120 20 250 90 520 40" fill="none" stroke="var(--brand-blue)" stroke-width="4"/>
      <path d="M0 66 C130 34 260 104 520 56 L520 120 L0 120 Z" fill="var(--brand-green)"/>
    </svg>
    <p class="web">www.maplehillkidz.com</p>
  </section>

  <section class="card card--back-white" aria-label="Business card back, white">
    <div class="brand"><span class="brand__dot"></span><span class="brand__name">Maple Hill</span></div>
    <div class="tagline-band">Learn, Explore, Bloom</div>
    <div class="rule"></div>
  </section>

  <section class="card card--back-blue" aria-label="Business card back, blue">
    <div class="brand"><span class="brand__dot"></span><span class="brand__name">Maple Hill</span></div>
    <div class="tagline-band">Learn, Explore, Bloom</div>
  </section>

  <section class="card card--back-green" aria-label="Business card back, green">
    <div class="brand"><span class="brand__dot"></span><span class="brand__name">Maple Hill</span></div>
    <div class="tagline-band">Learn, Explore, Bloom</div>
    <div class="rule"></div>
  </section>
</body>
</html>
```